Fun, Clean Business Card For Family Focused Travel Agency

I need a business card using specific colors and fonts as in the uploaded files. Ideally, I would like a large image of the logo on the back and all the contact info on the front. Maybe the stars/dots somewhere in a flowy form.

I do want it the contact information to be clear and easy to read. I don't want it to look too busy. Maybe even a bit minimalist.

I plan or ordering the ROUNDED CORNER business cards from Cardwell Press, so please consider that in your design.

Target Market(s)

Families with children, couples, groups of friends

Contact Information for Business Card

Marla Quint, Owner
Marla@TumbleTrips.example
Cell Phone Number 555-218-4603
Office Phone Number 555-647-1925
Specializing in Glimmerland destinations, Pelican Bay Fun Park, Cruises and All-Inclusive Vacations.

Nice but not required:
www.TumbleTrips.example
Facebook, Instagram, Twitter icons with username: TumbleTrips

Font styles to use
Sans Serif

Requirements
Must have
• Please try to use the colors from the logo as much as possible. I understand lighter shades/colors may be needed for some things.
Should not have
• NO SERIF FONTS. That is really the only thing I do not want at all

```html
<!DOCTYPE html>
<html lang="en">
<head>
<meta charset="utf-8">
<title>Tumble Trips — Business Card</title>
<link rel="stylesheet" href="https://fonts.googleapis.com/css2?family=Open+Sans:wght@300;400;600;700&display=swap">
<style>
  :root {
    --ink: #262a3a;
    --teal: #3dbb9c;
    --gold: #e7b23a;
    --sky: #3b8fd4;
    --coral: #f08a3b;
    --paper: #ffffff;
    --backdrop: #ecebe7;
    --muted: #6b6f7a;
  }
  * { box-sizing: border-box; margin: 0; padding: 0; }
  html, body {
    width: 1200px; height: 800px; overflow: hidden;
    background: var(--backdrop);
    font-family: "Open Sans", Arial, sans-serif;
    color: var(--ink);
  }
  .sheet { position: relative; width: 1200px; height: 800px; }

  .card {
    position: absolute; top: 245px;
    width: 540px; height: 310px;
    background: var(--paper);
    border-radius: 22px;
    box-shadow: 0 6px 18px rgba(0,0,0,.12);
    overflow: hidden;
  }
  .card--brand { left: 45px; }
  .card--contact { left: 615px; }

  /* brand side */
  .confetti {
    position: absolute; left: 70px; top: 70px;
    width: 150px; height: 110px; border-radius: 50%;
    background: radial-gradient(circle, rgba(61,187,156,.18), rgba(231,178,58,.12) 55%, rgba(255,255,255,0) 75%);
  }
  .brand-name {
    position: absolute; left: 0; right: 0; top: 88px;
    text-align: center;
    font-weight: 700; font-size: 58px; letter-spacing: -1px;
    color: var(--ink);
  }
  .specialty-lead {
    position: absolute; left: 0; right: 0; top: 180px;
    text-align: center;
    font-weight: 600; font-size: 15px; color: var(--teal);
  }
  .specialty-list {
    position: absolute; left: 20px; right: 20px; top: 222px;
    text-align: center;
    font-size: 13.5px; font-weight: 400; color: var(--ink);
  }
  .specialty-list .star { font-size: 12px; margin: 0 3px; }
  .star--gold { color: var(--gold); }
  .star--sky { color: var(--sky); }
  .star--coral { color: var(--coral); }

  /* contact side */
  .holder { position: absolute; left: 250px; top: 42px; }
  .holder-name { font-weight: 700; font-size: 24px; line-height: 1.1; }
  .holder-role { font-weight: 300; font-size: 22px; color: var(--teal); line-height: 1.15; }
  .contact-list { list-style: none; margin-top: 18px; }
  .contact-list li {
    display: flex; align-items: center; gap: 9px;
    font-size: 14px; line-height: 24px; color: var(--ink);
  }
  .contact-list svg { width: 14px; height: 14px; fill: var(--teal); flex: none; }
  .social { margin-top: 10px; }
  .social-handle { display: flex; align-items: center; gap: 9px; font-size: 14px; line-height: 22px; }
  .social-mark { width: 13px; height: 13px; background: var(--teal); border-radius: 2px; }
  .website { font-size: 14px; color: var(--teal); line-height: 22px; }
  .contact-confetti {
    position: absolute; left: 20px; top: 175px;
    width: 110px; height: 90px; border-radius: 50%;
    background: radial-gradient(circle, rgba(240,138,59,.16), rgba(59,143,212,.1) 55%, rgba(255,255,255,0) 75%);
  }
  .contact-brand {
    position: absolute; left: 40px; top: 220px;
    font-weight: 700; font-size: 34px; letter-spacing: -.5px; color: var(--ink);
  }
</style>
</head>
<body>
<main class="sheet">
  <section class="card card--brand" aria-label="Card back with brand name">
    <div class="confetti" role="img" aria-label="Scattered colourful stars and dots"></div>
    <h1 class="brand-name">TumbleTrips</h1>
    <p class="specialty-lead">Specializing in</p>
    <p class="specialty-list">
      <span class="star star--gold">★</span>Glimmerland destinations
      <span class="star star--sky">★</span>Pelican Bay Fun Park
      <span class="star star--coral">★</span>Cruises and All-Inclusive Vacations
    </p>
  </section>

  <section class="card card--contact" aria-label="Card front with contact details">
    <div class="holder">
      <h2 class="holder-name">Marla Quint</h2>
      <p class="holder-role">Owner</p>
      <ul class="contact-list">
        <li>
          <svg viewBox="0 0 14 14" aria-hidden="true"><path d="M4 0h6a1.5 1.5 0 0 1 1.5 1.5v11A1.5 1.5 0 0 1 10 14H4a1.5 1.5 0 0 1-1.5-1.5v-11A1.5 1.5 0 0 1 4 0zm0 2v9h6V2zm3 10a.8.8 0 1 0 0 .01z"/></svg>
          555-218-4603
        </li>
        <li>
          <svg viewBox="0 0 14 14" aria-hidden="true"><path d="M1 4c0-2 2.5-3 6-3s6 1 6 3v1.5H10V4.2C9 3.7 8 3.6 7 3.6S5 3.7 4 4.2v1.3H1zM3 7h8l2 6H1zm4 1.3a2 2 0 1 0 0 4 2 2 0 0 0 0-4z"/></svg>
          555-647-1925
        </li>
        <li>
          <svg viewBox="0 0 14 14" aria-hidden="true"><path d="M0 2.5h14v9H0zm1.3 1.2v.3L7 8l5.7-4v-.3zm0 1.8v4.8h11.4V5.5L7 9.5z"/></svg>
          Marla@TumbleTrips.example
        </li>
      </ul>
      <div class="social">
        <p class="social-handle"><span class="social-mark" aria-hidden="true"></span>TumbleTrips</p>
        <p class="website">www.TumbleTrips.example</p>
      </div>
    </div>
    <div class="contact-confetti" role="img" aria-label="Scattered colourful stars and dots"></div>
    <p class="contact-brand">TumbleTrips</p>
  </section>
</main>
</body>
</html>
```